Flyer to advertise gutter cleaning throughout the Autumn and winter monthss

I need a new flyer to advertise gutter and driveway cleaning, roof and gutter repairs.

I am an experienced licensed Plumber and Gasfitter looking to broaden my scope of work to gutter cleaning. I am experienced in cleaning gutter and live in a area with large gum trees. I wont something that's clear, eye catching but not too busy.

Flyer requirements: Free roof inspection - no obligation. Gutter Cleaning from $199. Pictures of men using blower or hands to clean roof gutters (no obvious faces) to be included. Australian looking houses.

A mention that 'All general plumbing maintenance' is offered as other services but not too much wording about this as the target is for gutter cleaning.

Phone number: 0427 385 912 (in this format)
Business Name: Larkvale Plumbing & Gasfitting
License: 3175420
ABN: 71364058227
Web: http://larkvaleplumbing.example.site/

Target Market(s)

Elderly - busy working class

Industry/Entity Type

Plumber

Font styles to use
Sans Serif

Colors
0355a3
fbed22
ec1f27
f78f20

Requirements
Must have
• Roof Gutter Cleaning pictures
• Men in protective clothing if possible
Nice to have
• More information:
• Prevent against flooding, mold, rust, rotting and corrosion now!
• Gutter Cleaning Services
• • Remove leaves, sticks, and other debris
• • Clear away clogs
• • Test your downpipes
• • Pinpoint any gutter issues
• • Repair gutter
• With regular service, you can count on your property to be well-protected no matter what the forecast!
Should not have
• Houses that don't look Australian

```html
<!DOCTYPE html>
<html lang="en">
<head>
<meta charset="utf-8">
<title>Larkvale Plumbing &amp; Gasfitting – Gutter Cleaning Flyer</title>
<link rel="stylesheet" href="https://fonts.googleapis.com/css2?family=Bebas+Neue&family=League+Gothic&family=Montserrat:wght@400;500;600&family=Roboto+Slab:wght@400&display=swap">
<style>
  :root {
    --backdrop: #ababab;
    --paper: #ffffff;
    --navy: #0b3592;
    --brand-red: #e91e4f;
    --roof-red: #d8453f;
    --sky: #62aef2;
    --seal-yellow: #f6e326;
    --ink: #222222;
  }
  * { box-sizing: border-box; margin: 0; padding: 0; }
  html, body { width: 1034px; height: 1200px; overflow: hidden; }
  body { background: var(--backdrop); position: relative; font-family: "Montserrat", sans-serif; }

  .flyer {
    position: absolute; left: 112px; top: 27px;
    width: 810px; height: 1145px;
    background: var(--paper); overflow: hidden;
  }
  .roof-photo {
    position: absolute; left: 0; top: 0; width: 810px; height: 520px;
    background: linear-gradient(180deg, var(--sky) 0%, var(--sky) 12%, var(--roof-red) 30%, #c93b36 80%, #7a4a30 100%);
  }
  .shapes { position: absolute; left: 0; top: 0; width: 810px; height: 1145px; }

  .offer { position: absolute; left: 57px; color: #fff; font-family: "League Gothic", sans-serif; line-height: 1; letter-spacing: 0.5px; text-shadow: 0 2px 4px rgba(0,0,0,.35); }
  .offer-service { font-size: 54px; }
  .offer-price { font-size: 92px; margin-top: -4px; }
  .offer--gutter { top: 102px; }
  .offer--driveway { top: 236px; }

  .seal { position: absolute; left: 525px; top: 112px; width: 140px; height: 140px; border-radius: 50%; background: var(--seal-yellow); display: flex; flex-direction: column; align-items: center; justify-content: center; font-family: "League Gothic", sans-serif; color: #111; line-height: 1.05; font-size: 24px; letter-spacing: 0.5px; }

  .inspection { position: absolute; left: 52px; top: 382px; width: 297px; height: 166px; background: var(--brand-red); border-radius: 4px; color: #fff; padding: 12px 0 0 30px; }
  .inspection-title { font-family: "Bebas Neue", sans-serif; font-size: 57px; line-height: 0.95; letter-spacing: 1.5px; }
  .inspection-note { font-family: "Roboto Slab", serif; font-size: 22px; letter-spacing: 1px; margin-top: 2px; }

  .benefits { position: absolute; left: 55px; top: 590px; list-style: none; font-size: 19px; color: var(--ink); line-height: 30px; }
  .benefits li { display: flex; align-items: center; }
  .tick { width: 18px; height: 18px; margin-right: 14px; flex: none; }
  .tick--inline { margin-left: 8px; margin-right: 10px; }

  .result { position: absolute; top: 545px; width: 124px; height: 124px; border-radius: 50%; border: 2px solid #8a8a8a; display: flex; align-items: center; justify-content: center; font-weight: 600; font-size: 17px; }
  .result--before { left: 504px; background: radial-gradient(circle, #6e6f72, #3f4043); color: #fff; }
  .result--after { left: 644px; background: radial-gradient(circle, #f3dcc3, #dcc0a2); color: #111; }

  .call { position: absolute; left: 60px; top: 722px; color: var(--navy); font-family: "League Gothic", sans-serif; line-height: 1; }
  .call-lead { font-size: 52px; letter-spacing: 0.3px; }
  .call-number { font-size: 76px; letter-spacing: 0.5px; margin-top: -2px; }

  .worker-photo { position: absolute; left: 518px; top: 716px; width: 168px; height: 363px; border-radius: 40px 40px 10px 10px; background: linear-gradient(180deg, #c9c9c9 0%, #5a5b60 35%, #6b5544 70%, #4b3a2d 100%); }
  .paving-photo { position: absolute; left: 0; top: 0; }

  .brand { position: absolute; left: 28px; top: 846px; display: flex; align-items: center; }
  .brand-mark { width: 166px; height: 166px; border-radius: 50%; background: var(--navy); border: 6px solid #fff; flex: none; }
  .brand-name { margin-left: 10px; font-weight: 600; font-size: 25px; line-height: 1.1; color: #111; letter-spacing: -0.3px; }

  .web { position: absolute; left: 42px; top: 1052px; color: #fff; font-size: 33px; font-weight: 500; }
  .reg { position: absolute; top: 1096px; color: #fff; font-size: 17px; font-weight: 500; }
  .reg--licence { left: 44px; }
  .reg--abn { left: 259px; }
  .social { position: absolute; left: 584px; top: 1092px; display: flex; gap: 4px; }
  .social span { width: 30px; height: 30px; border-radius: 50%; background: #fff; display: block; }
</style>
</head>
<body>
<article class="flyer">
  <div class="roof-photo" role="img" aria-label="Red tiled Australian roof with metal flue against blue sky"></div>

  <svg class="shapes" viewBox="0 0 810 1145" aria-hidden="true">
    <path d="M0,325 Q170,520 470,540 Q680,540 810,470 L810,500 Q680,575 470,575 Q170,560 0,362 Z" fill="var(--navy)"/>
    <path d="M0,345 Q170,545 470,562 Q680,565 810,492 L810,1145 L0,1145 Z" fill="var(--paper)"/>
  </svg>

  <div class="offer offer--gutter">
    <div class="offer-service">GUTTER CLEANING</div>
    <div class="offer-price">FROM $199</div>
  </div>
  <div class="offer offer--driveway">
    <div class="offer-service">DRIVEWAY CLEANING</div>
    <div class="offer-price">FROM $299</div>
  </div>

  <div class="seal">
    <span>SERVICE</span>
    <span>GUARANTEED</span>
    <span>QUALITY</span>
  </div>

  <div class="inspection">
    <div class="inspection-title">FREE ROOF<br>INSPECTION</div>
    <div class="inspection-note">NO OBLIGATION.</div>
  </div>

  <ul class="benefits">
    <li><svg class="tick" viewBox="0 0 18 18"><path d="M2,10 L7,15 L16,3" fill="none" stroke="#111" stroke-width="2"/></svg>Fully Insured<svg class="tick tick--inline" viewBox="0 0 18 18"><path d="M2,10 L7,15 L16,3" fill="none" stroke="#111" stroke-width="2"/></svg>Fast &amp; Safe</li>
    <li><svg class="tick" viewBox="0 0 18 18"><path d="M2,10 L7,15 L16,3" fill="none" stroke="#111" stroke-width="2"/></svg>Quality &amp; satisfaction<svg class="tick tick--inline" viewBox="0 0 18 18"><path d="M2,10 L7,15 L16,3" fill="none" stroke="#111" stroke-width="2"/></svg>Free inspection</li>
    <li><svg class="tick" viewBox="0 0 18 18"><path d="M2,10 L7,15 L16,3" fill="none" stroke="#111" stroke-width="2"/></svg>Professional &amp; affordable</li>
    <li><svg class="tick" viewBox="0 0 18 18"><path d="M2,10 L7,15 L16,3" fill="none" stroke="#111" stroke-width="2"/></svg>Kid &amp; pet friendly</li>
  </ul>

  <div class="result result--before" role="img" aria-label="Dirty grey paving before cleaning">BEFORE</div>
  <div class="result result--after" role="img" aria-label="Clean beige paving after cleaning">AFTER</div>

  <div class="call">
    <div class="call-lead">CALL US FOR A FREE</div>
    <div class="call-number">0427 385 912</div>
  </div>

  <svg class="paving-photo" width="810" height="1145" viewBox="0 0 810 1145" role="img" aria-label="Dark paved driveway with foliage">
    <defs>
      <linearGradient id="paving" x1="0" y1="0" x2="0" y2="1">
        <stop offset="0" stop-color="#5e5f61"/>
        <stop offset="1" stop-color="#3a3b3d"/>
      </linearGradient>
    </defs>
    <path d="M0,842 Q160,1005 420,1005 Q650,1005 810,925 L810,1145 L0,1145 Z" fill="url(#paving)"/>
    <path d="M0,842 Q160,985 420,985 Q650,985 810,905 L810,925 Q650,1005 420,1005 Q160,1005 0,862 Z" fill="var(--brand-red)"/>
  </svg>

  <div class="worker-photo" role="img" aria-label="Tradesman in cap and work clothes pressure-cleaning the driveway, seen from behind"></div>

  <div class="brand">
    <span class="brand-mark"></span>
    <span class="brand-name">LARKVALE PLUMBING<br>&amp; GASFITTING</span>
  </div>

  <div class="web">LarkvalePlumbing.com</div>
  <div class="reg reg--licence">License: 3175420</div>
  <div class="reg reg--abn">ABN: 71364058227</div>
  <div class="social" aria-label="Social media links"><span></span><span></span><span></span><span></span><span></span></div>
</article>
</body>
</html>
```